Leaflet to promote a new sports massage business

I am a Remedial and Sports Massage therapist and treat a range of people from professionals who spend hours working behind computers and have associated neck and back pain through poor posture to amateur sports people of varying intensity/ability - who encounter injuries along the way, or just need some good old stretching out.Remedial and sports massage helps people who have musculoskeletal injury, pain or dysfunction brought about by the stresses and strains of life. Through massage i can reduce pain, promote recovery after injury, relieve stress, and improve flexibility. All of this contributes to helping people feel better. I have just started working at a new location (address attached) and am looking to raise awareness that I am there and to promote the benefits of massage to encourage new clients(attached as a separate document). I have a business card (attached to the brief) which uses hands as the main device, I would like to include these – possibly in some sort of logo and I would like to use purple as a key colour (if colour is used). I also want to include the KTVB logo (attached) to add credibility

```html
<!DOCTYPE html>
<html lang="en">
<head>
<meta charset="utf-8">
<title>Helena Marsden – Remedial and Sports Massage</title>
<link href="https://fonts.googleapis.com/css2?family=Mulish:wght@400;600;700;800&display=swap" rel="stylesheet">
<style>
  :root {
    --purple-deep: #4d1649;
    --purple-mid: #9b4f99;
    --purple-bright: #8a3597;
    --purple-light: #c58bc4;
    --pink-soft: #f1d6ec;
    --lilac: #e7cfe6;
    --white: #ffffff;
    --page: #ffffff;
  }
  html, body {
    margin: 0;
    width: 1200px;
    height: 1000px;
    overflow: hidden;
    background: var(--page);
    font-family: "Mulish", sans-serif;
  }
  .leaflet {
    position: absolute;
    left: 337px;
    top: 4px;
    width: 534px;
    height: 755px;
    overflow: hidden;
    outline: 1px solid #e2d4e2;
  }
  .leaflet-art {
    position: absolute;
    inset: 0;
  }
  .header-text {
    position: absolute;
    left: 130px;
    right: 0;
    top: 24px;
    text-align: center;
    color: var(--white);
  }
  .therapist-name {
    margin: 0;
    font-size: 31px;
    font-weight: 600;
    letter-spacing: 1px;
    line-height: 36px;
  }
  .service-title {
    margin: 0;
    font-size: 21px;
    font-weight: 600;
    line-height: 26px;
  }
  .address {
    margin: 10px 0 0;
    font-size: 14.5px;
    line-height: 18px;
    font-style: normal;
  }
  .contact {
    list-style: none;
    margin: 8px 0 0;
    padding: 0;
    font-size: 14.5px;
    line-height: 17px;
  }
  .contact li {
    display: flex;
    justify-content: center;
    align-items: center;
    gap: 4px;
  }
  .contact svg { flex: none; }
  .benefits {
    position: absolute;
    left: 170px;
    width: 320px;
    top: 594px;
    text-align: center;
  }
  .benefits-title {
    margin: 0 0 4px;
    font-size: 23px;
    font-weight: 700;
    color: var(--purple-deep);
    letter-spacing: 0.3px;
  }
  .benefit-list {
    list-style: none;
    margin: 0;
    padding: 0;
    font-size: 15px;
    font-weight: 700;
    line-height: 18px;
  }
  .benefit-list li { color: var(--purple-deep); }
  .benefit-list li.accent { color: var(--purple-bright); font-weight: 600; }
  .benefit-list li::before {
    content: "";
    display: inline-block;
    width: 6px;
    height: 6px;
    margin-right: 6px;
    border-radius: 50%;
    background: var(--purple-light);
    border: 1px solid #8c6c8c;
    vertical-align: 2px;
  }
  .accreditation {
    position: absolute;
    left: 46px;
    top: 609px;
    width: 100px;
    height: 100px;
    border-radius: 50%;
    background: var(--white);
    box-shadow: 0 0 0 4px var(--lilac);
    display: flex;
    align-items: center;
    justify-content: center;
    font-size: 20px;
    font-weight: 700;
    letter-spacing: 2px;
    color: var(--purple-deep);
  }
</style>
</head>
<body>
<main class="leaflet">
  <svg class="leaflet-art" width="534" height="755" viewBox="0 0 534 755">
    <defs>
      <linearGradient id="header-fill" x1="0" y1="0" x2="1" y2="1">
        <stop offset="0" stop-color="#b07ab0"/>
        <stop offset="0.6" stop-color="#9d5a9c"/>
        <stop offset="1" stop-color="#8e418d"/>
      </linearGradient>
      <linearGradient id="lower-fill" x1="0" y1="0" x2="1" y2="1">
        <stop offset="0" stop-color="#f6dcef"/>
        <stop offset="0.5" stop-color="#eacbe6"/>
        <stop offset="1" stop-color="#c89bc8"/>
      </linearGradient>
      <linearGradient id="photo-fill" x1="0" y1="0" x2="1" y2="1">
        <stop offset="0" stop-color="#e9e6e6"/>
        <stop offset="0.5" stop-color="#b9c9d8"/>
        <stop offset="1" stop-color="#8a8f98"/>
      </linearGradient>
    </defs>
    <rect class="lower-background" width="534" height="755" fill="url(#lower-fill)"/>
    <path d="M0,700 C160,760 360,700 534,640 V755 H0 Z" fill="#f7ecf5" opacity="0.7"/>
    <path d="M0,560 C150,630 380,620 534,470 V520 C380,660 150,650 0,600 Z" fill="#d8a7d4" opacity="0.6"/>
    <path class="header-band" d="M0,0 H534 V190 C420,245 200,220 0,240 Z" fill="url(#header-fill)"/>
    <path d="M0,240 C200,220 420,245 534,190 V245 C420,250 200,235 0,250 Z" fill="#f3d3ea"/>
    <g role="img" aria-label="Illustration of two overlapping hands in deep purple">
      <path d="M0,70 C40,40 120,40 150,90 C180,140 190,190 200,222 L0,238 Z" fill="#5a1c58" opacity="0.9"/>
    </g>
    <g role="img" aria-label="Photo of a therapist massaging the shoulder of a woman lying on her side on a treatment mat">
      <path d="M0,240 C200,225 420,240 534,222 V480 C430,560 300,590 230,575 C120,555 40,470 0,385 Z" fill="url(#photo-fill)"/>
      <path d="M0,385 C40,470 120,555 230,575 C300,590 430,560 534,480" fill="none" stroke="#ffffff" stroke-width="2.5"/>
    </g>
  </svg>

  <header class="header-text">
    <h1 class="therapist-name">HELENA MARSDEN</h1>
    <p class="service-title">REMEDIAL AND SPORTS MASSAGE</p>
    <address class="address">Peak Motion Physiotherapy<br>Linden Sports Ground, Elm Park Road<br>Ashford&nbsp; AB1 2CD</address>
    <ul class="contact">
      <li><svg width="16" height="11" viewBox="0 0 16 11"><path d="M1,4 C1,1 15,1 15,4 L12,5 L11,3 H5 L4,5 Z M4,6 H12 L13,10 H3 Z" fill="#5a1c58"/></svg>07700 900123</li>
      <li><svg width="18" height="11" viewBox="0 0 18 11"><rect x="0.5" y="0.5" width="17" height="10" fill="#5a1c58"/><path d="M1,1 L9,6 L17,1" fill="none" stroke="#c58bc4"/></svg>helenamarsden@mailbox.example</li>
      <li><svg width="14" height="14" viewBox="0 0 14 14"><rect width="14" height="14" fill="#3b5a9a"/></svg>social.example/HelenaMarsdenMassage</li>
    </ul>
  </header>

  <div class="accreditation">KTVB</div>

  <section class="benefits">
    <h2 class="benefits-title">BENEFITS OF MASSAGE</h2>
    <ul class="benefit-list">
      <li>Reduces Pain</li>
      <li class="accent">Promotes Recovery</li>
      <li>Improves Posture And Flexibility</li>
      <li class="accent">Relieves Stress</li>
      <li>Improves Health And Wellbeing</li>
    </ul>
  </section>
</main>
</body>
</html>
```